Brellix Dwellings from US$9,995– Making buying a house as easy as ordering a pizza online - worldwide

I am after a website that is fun and interactive.

Buying a house should be as simple as buying a Pizza delivery online.....

Tidewell 20' ………………………………………….US$9,995
Standard, 30sqm Studio with kitchen & Bathroom, Flat Roof
Amber Ridge 20' ………………………………………….US$11,995
Standard, 30sqm Studio with kitchen & Bathroom, Pitched Roof
Lanternfield 40' ………………………………………….US$18,995
Standard, 60sqm, 2 Bedrooms, Lounge, kitchen & Bathroom, Flat Roof
Quillmoor 40' ………………………………………….US$20,995
Standard, 60sqm, 2 Bedrooms, Lounge, kitchen & Bathroom, Pitched Roof
Saltmeadow 40' ………………………………………….US$22,995
Beach design, 60sqm, 2 Bedrooms, Lounge, kitchen & Bathroom, Pitched Roof
The Brightfold 40' ………………………………………….US$24,995
Beach design, 60sqm, 2 Bedrooms, Lounge, kitchen, Bathroom, Deck, Pitched Roof

eg. https://www.grubtally.com.au/ https://www.crustvane.com

I want a fun design....

i want to reinvent how people DESIGN - BUILD and DELIVER housing

I want a SaaS solution for drop shipping pre-built houses.

The main campaign, we are offering 1,000 homes (to anywhere in the world) for US$9,995 + shipping

Just need to Pay a Fully refundable $100 Deposit to pre-register (so need a shopping cart & payment solution).

"Lane Skipper" - pay in full and jump the queue to get your Brellix months earlier.

The campaign is based on crowdsourcing - we need 1000 participants to pre-register - then everyone's orders will be filled .

The design is very simple...
HEADER
- The Story
- The Product
- Design our Own
- Pre-Register
- Contact Us

- Login
- Shopping Cart

FOOTER
- Privacy
- Terms & Conditions
- Investment
- Media
- NGO/Government
- Contact
- Sitemap

The important parts is that everyone who
- Subscribes
- Makes Contact
- Pre-registers
…in the system automatically gets an account (just need name and email address).
The user is then sent an email with details on how they can log back in at any time and see purchases, update profile (eg. Shipping address, contact details, etc....)

This data also needs to be sent to a CRM eg Hubspot for marketing to automate regular updates to all users.

It also needs to link to Facebook, LinkedIn , TikTok, Instagram, Twitter

You can get sample content from our old website https://kestrelbuilds.sitevaultpages.com/ - Plus I have attached updated content in this Brief.

The hero image should be a slider with videos and images with links to "Call to Action"

PLEASE NOTE: that "brellix" is a brand new product that we pre build offsite so when it is delivered, it is ready to move in to. So we need a whole new look and a new style

This is a wordpress site to be hosted on my server - Once completed I need full access to add, amend and update any pages, images products

I am very open to different colours - do not be limited by the colours in the logo.

I would be interested to see what you can do with NO white backgrounds. (This might look good or could look horrible)

And most importantly what will your design look like on mobile devices (phones / ipads)

SUCCESS (1) is getting the user to LOOK - DREAM - BUY (Or at least pre-register)

SUCCESS (2) it MUST look fun but still highly professional and TRUSTWORTHY to get the interest of investors to invest millions $$$$$

SUCCESS (3) we need to get "Inflencers / Bloggers" talking about Brellix - this could be done by a campaign to get a million likes and get a FREE home fo both the follower and the blogger

Target Market(s)

New home buyers (younger demographic), Families wanting to extend (middle aged)

Industry/Entity Type

Housing, Crowdsourcing, Drop shipping, SaaS technology

Coding

Coded - Design and coding required

Colors
0054AA
0677BA
7BADD7
CADEEF
E8F1F8
EE7325
F08F49
F5BC92
FAE3D3
FDF4ED

Requirements
Must have
• ecommerce, user accounts, social media & crm connections for crowdsourcing marketing, Call to actions
Nice to have
• $1,000,000
Should not have
• Do NOT complicate the funnel in the steps to sign-up

```html
<!DOCTYPE html>
<html lang="en">
<head>
<meta charset="utf-8">
<title>Brellix Dwellings</title>
<link rel="stylesheet" href="https://fonts.googleapis.com/css2?family=Open+Sans:wght@400;600;700;800&display=swap">
<style>
:root{
  --blue-deep:#0054AA;
  --blue:#0677BA;
  --blue-mid:#7BADD7;
  --blue-soft:#CADEEF;
  --blue-pale:#E8F1F8;
  --navy:#0A2F6B;
  --orange:#EE7325;
  --orange-light:#F08F49;
  --orange-soft:#F5BC92;
  --white:#ffffff;
}
*{box-sizing:border-box;margin:0;padding:0}
html,body{width:1200px;height:3432px;overflow:hidden}
body{font-family:"Open Sans",Arial,sans-serif;color:var(--white);background:var(--blue-deep);position:relative}
.abs{position:absolute}
.btn{display:inline-block;background:var(--orange);color:var(--white);font-weight:700;font-size:13px;text-transform:uppercase;border-radius:22px;padding:10px 24px;letter-spacing:.5px}

/* hero */
.hero{position:absolute;left:0;top:0;width:1200px;height:620px;background:linear-gradient(180deg,#5f8fc4 0%,#9cbfe0 35%,#c9c1a6 62%,#6f8a45 82%,#4d6a2e 100%)}
.brand{left:40px;top:24px}
.brand-name{font-size:38px;font-weight:700;letter-spacing:1px;color:var(--white);line-height:1}
.topbar{left:580px;top:14px;display:flex;gap:14px;align-items:center}
.pill{border-radius:20px;font-size:13px;font-weight:600;padding:7px 18px}
.pill.ghost{background:var(--white);color:var(--navy)}
.pill.phone{background:var(--blue-deep);color:var(--white);display:flex;gap:8px;align-items:center;font-weight:700;font-size:15px}
.cart{display:flex;gap:6px;align-items:center;font-size:14px;font-weight:600}
.nav{left:620px;top:64px;display:flex;gap:42px;font-size:14px;font-weight:700;letter-spacing:.5px}
.offer{left:872px;top:280px;width:288px;padding:22px 22px 24px;background:rgba(10,47,107,.88)}
.offer h1{font-size:28px;line-height:1.18;font-weight:800}
.offer h1 span{color:var(--orange)}
.offer .ctas{display:flex;gap:14px;margin-top:18px}
.offer .btn{padding:9px 18px;font-size:12px}
.deposit{left:0;top:620px;width:1200px;height:40px;background:var(--orange);text-align:center;font-weight:700;font-size:17px;line-height:40px}

/* why */
.why{left:0;top:660px;width:1200px;height:640px;background:linear-gradient(180deg,var(--blue-deep),var(--blue))}
.why h2,.split h2{font-size:22px;font-weight:800;letter-spacing:.5px}
.why h2{position:absolute;left:120px;top:56px}
.features{position:absolute;left:120px;top:110px;width:590px;display:grid;grid-template-columns:1fr 1fr;column-gap:30px;row-gap:34px}
.feature{display:flex;gap:14px}
.feature .ico{flex:none;width:44px;height:44px;border-radius:50%;background:var(--orange);display:flex;align-items:center;justify-content:center}
.feature h3{font-size:13px;font-weight:800;margin-bottom:8px}
.feature p{font-size:11.5px;line-height:1.55;color:var(--blue-pale)}
.why-photo{left:740px;top:80px;width:324px;height:520px;border-radius:14px;border:4px solid var(--white);background:linear-gradient(180deg,#8bb3d9 0%,#b9c9d6 40%,#5e6f80 65%,#6f8d4c 100%)}

/* split rows */
.split{position:absolute;left:0;width:1200px}
.split p{font-size:12.5px;line-height:1.65;color:var(--blue-pale);margin:16px 0 20px}
.split .btn{padding:8px 18px;font-size:11px}
.licensed{top:1300px;height:400px;background:var(--blue)}
.ontime{top:1700px;height:360px;background:var(--blue-deep)}
.service{top:2060px;height:380px;background:var(--blue)}
.photo{position:absolute;border-radius:2px}

/* contact */
.contact{left:0;top:2440px;width:1200px;height:500px;background:linear-gradient(180deg,#0a4fa0,#0b4590)}
.contact h2{text-align:center;font-size:22px;font-weight:800;padding-top:44px}
.field{position:absolute;background:var(--white);border-radius:6px;color:#8a96a8;font-size:12px;padding:11px 16px;height:36px}
.contact .btn{position:absolute;left:556px;top:412px;padding:8px 22px}

/* newsletter */
.news{left:120px;top:2960px;width:960px;height:120px;background:var(--blue);border-radius:10px}
.news h2{position:absolute;left:44px;top:36px;font-size:20px;font-weight:800;line-height:1.2}
.news .field{top:42px}
.news .btn{position:absolute;left:776px;top:40px;padding:10px 32px;font-size:14px}

/* footer */
.footer{left:0;top:3100px;width:1200px;height:332px;background:linear-gradient(180deg,#0b4fa2,#0a3f86)}
.footer .brand{left:130px;top:110px}
.footer h4{font-size:13px;font-weight:800;margin-bottom:14px}
.footer li{list-style:none;font-size:11px;line-height:1.7;color:var(--blue-pale)}
.crow{display:flex;gap:10px;align-items:flex-start;font-size:11px;color:var(--blue-pale);line-height:1.5;margin-bottom:10px}
.crow .dot{flex:none;width:20px;height:20px;border-radius:50%;background:var(--white);display:flex;align-items:center;justify-content:center}
.social{display:flex;gap:8px}
.social span{width:22px;height:22px;border-radius:50%;background:var(--white)}
.pay{display:flex;gap:8px}
.pay span{width:34px;height:22px;border-radius:3px;background:var(--white)}
.copy{position:absolute;left:0;top:304px;width:1200px;text-align:center;font-size:11px;color:var(--blue-soft)}
</style>
</head>
<body>

<header class="hero" role="img" aria-label="Photo of a modern prefabricated home with a timber pergola deck on a lawn under a blue sky">
  <div class="abs brand"><div class="brand-name">Brellix</div></div>
  <div class="abs topbar">
    <span class="pill ghost">Call for a FREE Quote Today</span>
    <span class="pill phone"><svg width="14" height="14" viewBox="0 0 24 24" fill="#fff"><path d="M6.6 10.8a15 15 0 0 0 6.6 6.6l2.2-2.2a1 1 0 0 1 1-.25 11.4 11.4 0 0 0 3.6.57 1 1 0 0 1 1 1V20a1 1 0 0 1-1 1A17 17 0 0 1 3 4a1 1 0 0 1 1-1h3.5a1 1 0 0 1 1 1c0 1.25.2 2.45.57 3.57a1 1 0 0 1-.25 1z"/></svg>043 218 905</span>
    <span class="cart">Cart <svg width="22" height="20" viewBox="0 0 24 22" fill="none" stroke="#fff" stroke-width="2"><path d="M1 2h4l3 12h12l3-9H6"/><circle cx="9" cy="19" r="1.6" fill="#fff"/><circle cx="19" cy="19" r="1.6" fill="#fff"/></svg></span>
  </div>
  <nav class="abs nav"><span>THE STORY</span><span>THE PRODUCT</span><span>PRE-REGISTER</span><span>CONTACT US</span></nav>
  <div class="abs offer">
    <h1>WE ARE OFFERING 1,000 HOMES FOR <span>US$9,995</span> + SHIPPING</h1>
    <div class="ctas"><span class="btn">Pre-Register</span><span class="btn">Buy Now</span></div>
  </div>
</header>
<div class="abs deposit">Just need to Pay a Fully refundable $100 Deposit to pre-register</div>

<section class="abs why">
  <h2>WHY CHOOSE BRELLIX</h2>
  <div class="features">
    <div class="feature"><div class="ico"><svg width="22" height="22" viewBox="0 0 24 24" fill="none" stroke="#fff" stroke-width="2.2"><circle cx="12" cy="12" r="9"/><path d="M12 7v5l3 2"/></svg></div><div><h3>FAST CONSTRUCTION</h3><p>From the time the contract is signed and deposit is paid, we can have your home built and delivered in under 12 weeks.</p></div></div>
    <div class="feature"><div class="ico"><svg width="22" height="22" viewBox="0 0 24 24" fill="none" stroke="#fff" stroke-width="2.2"><path d="M12 3v18M16 7c0-1.7-1.8-3-4-3s-4 1.3-4 3 1.8 2.5 4 3 4 1.3 4 3-1.8 3-4 3-4-1.3-4-3"/></svg></div><div><h3>AFFORDABLE</h3><p>You can own your new home from under $10,000 and we supply the kitchen, bathroom, fit-out, labour and delivery as well.</p></div></div>
    <div class="feature"><div class="ico"><svg width="22" height="22" viewBox="0 0 24 24" fill="none" stroke="#fff" stroke-width="2.4"><path d="M5 12l5 5 9-10"/></svg></div><div><h3>QUALITY FIT-OUT</h3><p>We have sourced the best quality local and imported products to ensure you get the highest quality. If we don't have what you are after, just ask.</p></div></div>
    <div class="feature"><div class="ico"><svg width="22" height="22" viewBox="0 0 24 24" fill="none" stroke="#fff" stroke-width="2.2"><path d="M3 11l9-7 9 7M6 9v11h12V9"/></svg></div><div><h3>STRESS FREE BUILDING</h3><p>We have a team of specialists to help you through the whole process, from design and build through to delivery, so you never face it alone.</p></div></div>
    <div class="feature"><div class="ico"><svg width="22" height="22" viewBox="0 0 24 24" fill="none" stroke="#fff" stroke-width="2.2"><path d="M6 3h9l4 4v14H6z"/><path d="M9 12h7M9 16h7"/></svg></div><div><h3>MINIMAL PERMITS</h3><p>Every project is different but our homes are engineered to our strictest standards, so council approval is often simple and quick.</p></div></div>
    <div class="feature"><div class="ico"><svg width="22" height="22" viewBox="0 0 24 24" fill="none" stroke="#fff" stroke-width="2.2"><path d="M12 3l8 3v6c0 5-3.5 8-8 9-4.5-1-8-4-8-9V6z"/><path d="M8.5 12l2.5 2.5 4.5-5"/></svg></div><div><h3>10 YEAR GUARANTEE</h3><p>Australian regulations require builders to give a 7 year building warranty. We are so confident in our structures we give you 10 years.</p></div></div>
  </div>
  <div class="abs why-photo" role="img" aria-label="Photo of a two-storey modular home and a finished interior"></div>
</section>

<section class="split licensed">
  <div class="abs" style="left:128px;top:44px;width:300px">
    <h2>LICENSED CONTRACTORS</h2>
    <p>As a company dedicated to providing premier customer service, it is important to us to deliver unparalleled workmanship on every assignment. We are accredited, licensed, bonded and insured. With our experience and expertise, we can provide the support your project needs.</p>
    <span class="btn">Read More</span>
  </div>
  <div class="photo" style="left:600px;top:76px;width:472px;height:280px;background:linear-gradient(160deg,#fbe7b8 0%,#e9a55a 35%,#6f8fb8 70%,#3e5f8c 100%)" role="img" aria-label="Photo of a builder working on a timber roof frame at sunset"></div>
</section>

<section class="split ontime">
  <div class="photo" style="left:128px;top:24px;width:472px;height:276px;background:linear-gradient(180deg,#d9e4ec 0%,#b7c6d2 45%,#6e6a5f 70%,#7fa451 100%)" role="img" aria-label="Photo of a modular home with timber cladding and a deck on green grass"></div>
  <div class="abs" style="left:720px;top:90px;width:330px">
    <h2>ON-TIME COMPLETION</h2>
    <p>We will work with you to meet deadlines and coordinate with other related projects. We will maintain open communication with you to keep you up to date on the status of your job. We do this to guarantee that the project is completed according to your preferences.</p>
  </div>
</section>

<section class="split service">
  <div class="abs" style="left:128px;top:100px;width:300px">
    <h2>GREAT SERVICE</h2>
    <p>We combine our industry knowledge, the highest quality building supplies and equipment, and our dedication to deliver exceptional service to our clients. We will stay in touch, keeping you up to date on both the paperwork and renovation process.</p>
    <span class="btn">Read More</span>
  </div>
  <div class="photo" style="left:600px;top:20px;width:472px;height:300px;background:linear-gradient(180deg,#c8d3dc 0%,#9aa8b3 40%,#3a3f47 68%,#596d3f 100%)" role="img" aria-label="Photo of a dark clad pitched-roof home with lit windows at dusk"></div>
</section>

<section class="abs contact" role="img" aria-label="Faint photo of a modular home behind the contact form">
  <h2>CONTACT US</h2>
  <div class="field" style="left:232px;top:120px;width:360px">First Name</div>
  <div class="field" style="left:608px;top:120px;width:360px">Last Name</div>
  <div class="field" style="left:232px;top:192px;width:360px">Email Id</div>
  <div class="field" style="left:608px;top:192px;width:360px">Phone</div>
  <div class="field" style="left:232px;top:240px;width:736px;height:144px">Message</div>
  <span class="btn">Submit</span>
</section>

<section class="abs news">
  <h2>NEWSLETTER<br>SUBSCRIBE</h2>
  <div class="field" style="left:224px;width:250px">Name</div>
  <div class="field" style="left:490px;width:260px">Email Id</div>
  <span class="btn">Subscribe</span>
</section>

<footer class="abs footer">
  <div class="abs brand"><div class="brand-name">Brellix</div></div>
  <div class="abs" style="left:432px;top:40px;width:200px">
    <h4>CONTACT US</h4>
    <div class="crow"><span class="dot"><svg width="10" height="12" viewBox="0 0 24 28" fill="#0054AA"><path d="M12 0a9 9 0 0 0-9 9c0 7 9 19 9 19s9-12 9-19a9 9 0 0 0-9-9zm0 13a4 4 0 1 1 0-8 4 4 0 0 1 0 8z"/></svg></span><span>PO Box 418, Carrowen,<br>Victoria 3991, Australia</span></div>
    <div class="crow"><span class="dot"><svg width="10" height="10" viewBox="0 0 24 24" fill="#0054AA"><path d="M6.6 10.8a15 15 0 0 0 6.6 6.6l2.2-2.2a1 1 0 0 1 1-.25 11.4 11.4 0 0 0 3.6.57 1 1 0 0 1 1 1V20a1 1 0 0 1-1 1A17 17 0 0 1 3 4a1 1 0 0 1 1-1h3.5a1 1 0 0 1 1 1c0 1.25.2 2.45.57 3.57a1 1 0 0 1-.25 1z"/></svg></span><span>Call Us:<br>043 218 905</span></div>
    <div class="crow"><span class="dot"><svg width="11" height="9" viewBox="0 0 24 18" fill="none" stroke="#0054AA" stroke-width="2.5"><rect x="1" y="1" width="22" height="16"/><path d="M1 1l11 9 11-9"/></svg></span><span>E-mail Us:<br>info@brellix.com</span></div>
  </div>
  <div class="abs" style="left:672px;top:40px">
    <h4>LINKS</h4>
    <ul><li>PRIVACY</li><li>TERMS &amp; CONDITIONS</li><li>INVESTMENT</li><li>MEDIA</li><li>NGO/GOVERNMENT</li><li>CONTACT</li><li>SITEMAP</li></ul>
  </div>
  <div class="abs" style="left:888px;top:40px">
    <h4>FOLLOW US</h4>
    <div class="social"><span></span><span></span><span></span><span></span><span></span></div>
    <h4 style="margin-top:34px">SECURE PAYMENT</h4>
    <div class="pay"><span></span><span></span><span></span><span></span></div>
  </div>
  <div class="copy">Copyright © 2020 All Rights Reserved</div>
</footer>

</body>
</html>
```